Corporate Design für logopädische Praxis
Zielgruppe
Ich gründe eine logopädische Praxis, die Sprachtherapie sowohl für Erwachsene als auch Kinder anbietet und damit ein Logo benötigt, das jede Altersgruppe anspricht und 'Lindenhof' als fachliche und menschliche Qualitätszeit interpretiert.
Aufgabenstellung
Ich bevorzuge ein klares Design, welches das Wortspiel der 'Lindenhof' im Idealfall aufgreift und den Patienten vermittelt, dass sowohl die fachliche Qualität der Behandlung als auch die Ebene von Empathie und Patientenorientierung im zwischenmenschlichen Umgang für die Praxis zentral sind.

```html
<!DOCTYPE html>
<html lang="de">
<head>
<meta charset="utf-8">
<title>Lindenhof – Praxis für Logopädie · Geschäftsausstattung</title>
<link href="https://fonts.googleapis.com/css2?family=Montserrat:wght@300;400&display=swap" rel="stylesheet">
<style>
  :root{
    --brand:#a48ca9;
    --tagline:#a09aa3;
    --ink:#3d3b3e;
    --ink-soft:#6e6a70;
    --paper:#fbfbfb;
    --stage:#3f3f3f;
    --wave:#f1eff4;
    --rule:#cfc8d3;
  }
  *{margin:0;padding:0;box-sizing:border-box}
  html,body{width:1200px;height:2760px;overflow:hidden}
  body{position:relative;background:var(--paper);font-family:'Montserrat',Arial,sans-serif;font-weight:300;color:var(--ink)}
  .abs{position:absolute}
  .hero{left:0;top:0;width:1200px;height:977px;background:var(--paper)}
  .stage{left:0;top:977px;width:1200px;height:1783px;background:var(--stage)}
  .card,.letter{background:var(--paper);overflow:hidden}
  .card-front{left:191px;top:1035px;width:380px;height:245px}
  .card-back{left:629px;top:1035px;width:380px;height:245px}
  .letter{left:131px;top:1329px;width:938px;height:1327px}
  svg text{font-family:'Montserrat',Arial,sans-serif}
  .brand-name{fill:var(--brand);font-weight:300}
  .brand-tag{fill:var(--tagline);font-weight:300}
  .small{font-size:10.5px;color:var(--ink-soft);line-height:15px;white-space:nowrap}
  .card-name{font-size:11px;color:var(--ink-soft);letter-spacing:.3px}
  .contact-row{display:flex;align-items:center;gap:6px;height:16px}
  .dot{width:11px;height:11px;border-radius:50%;background:var(--brand);flex:none}
  .sender{font-size:9px;color:var(--ink-soft)}
  .address{font-size:15px;line-height:19px;color:var(--ink)}
  .body-text{font-size:15px;line-height:19px;color:var(--ink);width:700px}
  .body-text p{margin-bottom:19px}
  .fold{left:0;width:22px;height:1px;background:var(--ink-soft)}
  .signature{left:116px;top:996px;width:150px;height:76px;background:linear-gradient(90deg,#e8e9f1,#f3f3f7);border-radius:6px}
  .footer-col{font-size:11px;line-height:24.4px;color:var(--ink-soft);white-space:nowrap}
  .footer-col .contact-row{height:24.4px;gap:9px}
  .footer-col .dot{width:16px;height:16px}
  .divider{width:1px;height:107px;background:var(--rule);top:1180px}
</style>
</head>
<body>

<section class="abs hero" aria-label="Logo">
  <svg class="abs" style="left:0;top:0" width="1200" height="977" viewBox="0 0 1200 977">
    <text class="brand-name" x="330" y="536" font-size="108" textLength="536" lengthAdjust="spacingAndGlyphs">Lindenhof</text>
    <text class="brand-tag" x="452" y="580" font-size="31" letter-spacing="4" textLength="412" lengthAdjust="spacingAndGlyphs">Praxis für Logopädie</text>
  </svg>
</section>

<section class="abs stage" aria-label="Geschäftsausstattung"></section>

<article class="abs card card-front" aria-label="Visitenkarte Vorderseite">
  <svg class="abs" style="left:0;top:0" width="380" height="245" viewBox="0 0 380 245">
    <text class="brand-name" x="98" y="133" font-size="38" textLength="182" lengthAdjust="spacingAndGlyphs">Lindenhof</text>
    <text class="brand-tag" x="140" y="147" font-size="11" letter-spacing="1.5" textLength="140" lengthAdjust="spacingAndGlyphs">Praxis für Logopädie</text>
  </svg>
</article>

<article class="abs card card-back" aria-label="Visitenkarte Rückseite">
  <svg class="abs" style="left:0;top:0" width="380" height="245" viewBox="0 0 380 245">
    <text class="brand-name" x="36" y="101" font-size="42" textLength="208" lengthAdjust="spacingAndGlyphs">Lindenhof</text>
    <text class="brand-tag" x="85" y="115" font-size="12" letter-spacing="1.5" textLength="159" lengthAdjust="spacingAndGlyphs">Praxis für Logopädie</text>
  </svg>
  <div class="abs" style="left:34px;top:150px">
    <div class="card-name">MAX MUSTERMANN</div>
    <div class="small">Geschäftsführer</div>
    <div class="small" style="margin-top:18px">Musterweg 13</div>
    <div class="small">54321 Musterdorf</div>
  </div>
  <div class="abs small" style="left:210px;top:146px">
    <div class="contact-row"><span class="dot"></span>+49 (0)1234 5 67 89-0</div>
    <div class="contact-row"><span class="dot"></span>+49 (0)1234 5 67 89-50</div>
    <div class="contact-row"><span class="dot"></span>+49 (0)123 4 56 78 90</div>
    <div class="contact-row"><span class="dot"></span>info@yourcompany.de</div>
    <div class="contact-row"><span class="dot"></span>yourcompany.de</div>
  </div>
</article>

<article class="abs letter" aria-label="Briefbogen">
  <svg class="abs" style="left:0;top:0" width="938" height="1327" viewBox="0 0 938 1327">
    <path d="M0 1161 C 250 1150, 430 1110, 600 1030 C 720 975, 830 955, 938 952 L938 1327 L0 1327 Z" fill="var(--wave)"/>
    <text class="brand-name" x="532" y="147" font-size="74" textLength="333" lengthAdjust="spacingAndGlyphs">Lindenhof</text>
    <text class="brand-tag" x="605" y="174" font-size="21" letter-spacing="3" textLength="260" lengthAdjust="spacingAndGlyphs">Praxis für Logopädie</text>
  </svg>

  <div class="abs sender" style="left:116px;top:260px">Your Company | Musterweg 13 | 54321 Musterdorf</div>
  <div class="abs address" style="left:116px;top:280px">Max Mustermann<br>Musterstr. 1<br>12345 Muster</div>

  <div class="abs fold" style="top:468px"></div>
  <div class="abs fold" style="top:938px"></div>

  <div class="abs body-text" style="left:116px;top:458px">
    <p>Sehr geehrte Damen und Herren,</p>
    <p style="margin-top:38px">Lorem ipsum dolor sit amet, consetetur sadipscing elitr, sed diam nonumy eirmod tempor invidunt ut labore et dolore magna aliquyam erat, sed diam voluptua. At vero eos et accusam et justo duo dolores et ea rebum. Stet clita kasd gubergren, no sea takimata sanctus est Lorem ipsum dolor sit amet. Lorem ipsum dolor sit amet, consetetur sadipscing elitr, sed diam nonumy eirmod tempor invidunt ut labore et dolore magna aliquyam erat, sed diam voluptua. At vero eos et accusam et justo duo dolores et ea rebum. Stet clita kasd gubergren, no sea takimata sanctus est Lorem ipsum dolor sit amet. Lorem ipsum dolor sit amet, consetetur sadipscing elitr, sed diam nonumy eirmod tempor invidunt ut labore et dolore magna aliquyam erat, sed diam voluptua. At vero eos et accusam et justo duo dolores et ea rebum. Stet clita kasd gubergren, no sea takimata sanctus est Lorem ipsum dolor sit amet.</p>
    <p>Duis autem vel eum iriure dolor in hendrerit in vulputate velit esse molestie consequat, vel illum dolore eu feugiat nulla facilisis at vero eros et accumsan et iusto odio dignissim qui blandit praesent luptatum zzril delenit augue duis dolore te feugait nulla facilisi. Lorem ipsum dolor sit amet, consectetuer adipiscing elit, sed diam nonummy nibh euismod tincidunt ut laoreet dolore magna aliquam erat volutpat.</p>
    <p>Ut wisi enim ad minim veniam, quis nostrud exerci tation ullamcorper suscipit lobortis nisl ut aliquip ex ea commodo consequat. Duis autem vel eum iriure dolor in hendrerit in vulputate velit esse molestie consequat, vel illum dolore eu feugiat nulla facilisis at vero eros et accumsan et iusto odio dignissim qui blandit praesent luptatum zzril delenit augue duis dolore te feugait nulla facilisi.</p>
    <p style="margin-top:38px">Mit freundlichen Grüßen</p>
  </div>

  <div class="abs signature" role="img" aria-label="Handschriftliche Unterschrift"></div>

  <div class="abs footer-col" style="left:116px;top:1185px">
    <div class="contact-row"><span class="dot"></span>+49 (0)1234 5 67 89-0</div>
    <div class="contact-row"><span class="dot"></span>+49 (0)1234 5 67 89-50</div>
    <div class="contact-row"><span class="dot"></span>info@yourcompany.de</div>
    <div class="contact-row"><span class="dot"></span>yourcompany.de</div>
  </div>
  <div class="abs divider" style="left:284px"></div>
  <div class="abs footer-col" style="left:308px;top:1185px">MAX MUSTERMANN<br>Geschäftsführer<br>Musterweg 13<br>54321 Musterdorf</div>
  <div class="abs divider" style="left:445px"></div>
  <div class="abs footer-col" style="left:471px;top:1185px">Talsparkasse<br>IBAN: DE43 XXXX 0110 XXXX 0481 XX<br>BIC: KRXXDE55XXX<br>Geschäftsführer: Max Mustermann</div>
  <div class="abs divider" style="left:685px"></div>
  <div class="abs footer-col" style="left:710px;top:1185px">Ust. ID: DE2XX9XX10X<br>HRB 1XX4XX<br>Amtsgericht Talbrück<br>Gesellschaftssitz: Weidenbach</div>
</article>

</body>
</html>
```